Computer consultant business card

Bexil Software is a newly started computer consulting company. It's a small one-man company that provides mostly Vornix applications but also websites in collaboration with designers. I'm running this company on the side of full time university studies.

I want the final design to be clean and memorable. Be creative! :)

Some inspiration:
http://www.pixelmarta.com/design/48317
http://www.pixelmarta.com/design/2739164/business-card-design-by-frostlynk
http://www.pixelmarta.com/design/604281/business-card-design-by-koralind-vestrabanu

See attachment for my company logo.
Updates

I would like to thank everyone for submitting! I'll need a couple of days to review and ultimately select a design.

Target Market(s)

Non-technical entrepreneurs and small companies.

Industry/Entity Type

University

Requirements
Must have
• My company logo.
In any way, both colors from my logo.
First- and last name, e-mail and phone number.
Double-sided design.
Nice to have
• Something creative with the symbol in my logo

```html
<!DOCTYPE html>
<html lang="en">
<head>
<meta charset="utf-8">
<title>Kivr Software – Business Card Set</title>
<link rel="stylesheet" href="https://fonts.googleapis.com/css2?family=Comfortaa:wght@700&family=Didact+Gothic&family=Open+Sans:wght@400;700&family=PT+Sans&display=swap">
<style>
  :root {
    --brand-blue: #4672b8;
    --brand-dark: #333132;
    --card-white: #ffffff;
    --card-black: #050505;
    --card-charcoal: #333132;
    --backdrop: #c7b9a4;
    --label-ink: #1b1b1b;
  }
  * { margin: 0; padding: 0; box-sizing: border-box; }
  html, body {
    width: 1200px; height: 788px; overflow: hidden;
    background: var(--backdrop);
  }
  .sheet { position: relative; width: 1200px; height: 788px; }

  .side-label {
    position: absolute; width: 527px; text-align: center;
    font-family: "PT Sans", sans-serif; font-size: 21px; color: var(--label-ink);
  }

  .card {
    position: absolute; width: 527px; height: 300px;
    border-radius: 22px; overflow: hidden;
    box-shadow: 0 3px 8px rgba(0,0,0,0.35);
  }
  .card--white { background: var(--card-white); }
  .card--black { background: var(--card-black); }
  .card--charcoal { background: var(--card-charcoal); }

  .brand { position: absolute; display: flex; align-items: center; }
  .brand__mark { border-radius: 50%; background: var(--brand-blue); flex: none; }
  .brand__name {
    font-family: "Comfortaa", sans-serif; font-weight: 700; line-height: 1;
    color: var(--brand-dark);
  }
  .card--black .brand__name, .card--charcoal .brand__name { color: var(--card-white); }

  .brand--small { left: 32px; top: 43px; gap: 20px; }
  .brand--small .brand__mark { width: 86px; height: 86px; }
  .brand--small .brand__name { font-size: 78px; margin-top: -6px; }

  .brand--large { left: 68px; top: 81px; gap: 28px; }
  .brand--large .brand__mark { width: 130px; height: 130px; }
  .brand--large .brand__name { font-size: 112px; margin-top: -8px; }

  .brand--medium { left: 100px; top: 92px; gap: 24px; }
  .brand--medium .brand__mark { width: 112px; height: 112px; }
  .brand--medium .brand__name { font-size: 98px; margin-top: -8px; }

  .website {
    position: absolute; left: 0; right: 0; text-align: center;
    font-family: "Didact Gothic", sans-serif; font-size: 19px; letter-spacing: 5.6px;
    color: var(--brand-dark);
  }
  .card--white .website { top: 249px; }
  .card--black .website, .card--charcoal .website { top: 254px; color: var(--card-white); }

  .name-band {
    position: absolute; left: 260px; top: 185px; width: 236px; height: 50px;
    background: var(--brand-blue); padding: 5px 0 0 6px; color: var(--card-white);
    font-family: "Open Sans", sans-serif;
  }
  .name-band__accent {
    position: absolute; left: 496px; top: 185px; width: 31px; height: 50px;
    background: var(--brand-dark);
  }
  .name-band__name { font-size: 17.5px; font-weight: 700; line-height: 22px; letter-spacing: 0.3px; white-space: nowrap; }
  .name-band__role { font-size: 12.5px; line-height: 18px; }

  .contact {
    position: absolute; left: 267px; top: 244px;
    font-family: "Open Sans", sans-serif; font-size: 13px; color: var(--brand-dark);
    list-style: none;
  }
  .contact__item { display: flex; align-items: center; gap: 8px; height: 18px; }
  .contact__icon { width: 10px; height: 10px; flex: none; }

  .glow-pattern {
    position: absolute; inset: 0;
    background:
      radial-gradient(ellipse 190px 95px at 170px 10px, rgba(120,120,120,0.45), transparent 75%),
      radial-gradient(ellipse 160px 115px at 420px 275px, rgba(130,125,135,0.5), transparent 75%);
  }
</style>
</head>
<body>
<main class="sheet">

  <div class="side-label" style="left:53px; top:33px;">Front</div>
  <div class="side-label" style="left:622px; top:33px;">Back - 1</div>
  <div class="side-label" style="left:53px; top:404px;">Back - 2</div>
  <div class="side-label" style="left:622px; top:404px;">Back - 3</div>

  <section class="card card--white" style="left:53px; top:74px;">
    <div class="brand brand--small">
      <span class="brand__mark"></span>
      <span class="brand__name">kivr</span>
    </div>
    <div class="name-band">
      <p class="name-band__name">First Name + Last Name</p>
      <p class="name-band__role">Designation</p>
    </div>
    <div class="name-band__accent"></div>
    <ul class="contact">
      <li class="contact__item">
        <svg class="contact__icon" viewBox="0 0 10 10"><path d="M2 0.5 L4 2.8 L3 4 Q4.5 6 6 7 L7.2 6 L9.5 8 L8 9.5 Q4 9 0.5 2 Z" fill="none" stroke="#333132" stroke-width="1"/></svg>
        <span>+12 345 6789</span>
      </li>
      <li class="contact__item">
        <svg class="contact__icon" viewBox="0 0 10 10"><rect x="0.5" y="2" width="9" height="6.5" fill="#333132"/><path d="M0.5 2 L5 5.5 L9.5 2" fill="none" stroke="#fff" stroke-width="0.9"/></svg>
        <span>info@website.com</span>
      </li>
    </ul>
  </section>

  <section class="card card--white" style="left:622px; top:74px;">
    <div class="brand brand--large">
      <span class="brand__mark"></span>
      <span class="brand__name">kivr</span>
    </div>
    <p class="website">www.website.com</p>
  </section>

  <section class="card card--black" style="left:53px; top:445px;">
    <div class="glow-pattern" role="img" aria-label="Soft metallic perforated dot texture glowing in the top left and bottom right corners"></div>
    <div class="brand brand--medium">
      <span class="brand__mark"></span>
      <span class="brand__name">kivr</span>
    </div>
    <p class="website">www.website.com</p>
  </section>

  <section class="card card--charcoal" style="left:622px; top:445px;">
    <div class="brand brand--large">
      <span class="brand__mark"></span>
      <span class="brand__name">kivr</span>
    </div>
    <p class="website">www.website.com</p>
  </section>

</main>
</body>
</html>
```